Business Card for Professional Photographer

I'm looking for an eye catching modern clean design that compliments my logo/ website fonts & colours.
I specialise in architecture, corporate & commercial photography so I'm marketing to professional clients rather than portrait / wedding clients.

I would prefer to not have a solid black design.

My logo brand guide is as follows :

Main front font. : Reislust
Main font colour : #fff
Slogan front font : Ubuntu Bold
Monogram front font : Venti Medium
Container colour : #fff

I need print ready files in pdf .png & .eps formats.

Included in the files below are some screen grabs as reference to font & colours etc.

```html
<!DOCTYPE html>
<html lang="en">
<head>
<meta charset="utf-8">
<title>Frame Line Studio – Business Card</title>
<link rel="stylesheet" href="https://fonts.googleapis.com/css2?family=Ubuntu:wght@400;500;700&family=Roboto:wght@400&family=Titillium+Web:wght@700&display=swap">
<style>
  :root {
    --backdrop: #2b2b2b;
    --card: #1c1c1e;
    --gold: #c9a24a;
    --silver: #8d8d90;
    --white: #ffffff;
  }
  * { margin: 0; padding: 0; box-sizing: border-box; }
  html, body { width: 799px; height: 1200px; overflow: hidden; }
  body {
    background: var(--backdrop);
    position: relative;
    font-family: "Roboto", sans-serif;
  }
  .card {
    position: absolute;
    left: 80px;
    width: 640px;
    height: 366px;
    background: var(--card);
    border-radius: 4px;
    box-shadow: 0 10px 30px rgba(0,0,0,0.45);
    overflow: hidden;
  }
  .card--front { top: 150px; }
  .card--back { top: 680px; }

  /* Front */
  .front-mark {
    position: absolute;
    left: 0; right: 0; top: 120px;
    display: flex; align-items: center; justify-content: center; gap: 14px;
  }
  .front-mark__square {
    width: 16px; height: 16px;
    background: var(--silver);
    flex: none;
  }
  .front-mark__name {
    font-family: "Ubuntu", sans-serif;
    font-weight: 500;
    font-size: 34px;
    letter-spacing: 4px;
    color: var(--silver);
    text-transform: uppercase;
  }
  .front-web {
    position: absolute;
    left: 0; right: 0; top: 270px;
    text-align: center;
    font-family: "Ubuntu", sans-serif;
    font-size: 15px;
    letter-spacing: 2.5px;
    color: var(--gold);
  }

  /* Back */
  .back-mark {
    position: absolute;
    left: 44px; top: 118px;
    display: flex; align-items: flex-start; gap: 12px;
  }
  .back-mark__square {
    width: 14px; height: 14px;
    margin-top: 8px;
    background: var(--gold);
    flex: none;
  }
  .back-mark__name {
    font-family: "Ubuntu", sans-serif;
    font-weight: 500;
    font-size: 28px;
    line-height: 38px;
    letter-spacing: 4px;
    color: var(--gold);
    text-transform: uppercase;
  }
  .brand {
    position: absolute;
    right: 34px; top: 56px;
    text-align: left;
  }
  .brand__name {
    font-family: "Ubuntu", sans-serif;
    font-size: 27px;
    letter-spacing: 5px;
    color: var(--gold);
    text-transform: uppercase;
    line-height: 1;
  }
  .brand__tagline {
    font-family: "Ubuntu", sans-serif;
    font-weight: 700;
    font-size: 10.5px;
    letter-spacing: 1.6px;
    color: var(--gold);
    margin-top: 4px;
  }
  .person {
    position: absolute;
    right: 34px; top: 160px;
    text-align: right;
  }
  .person__name {
    font-family: "Titillium Web", sans-serif;
    font-weight: 700;
    font-size: 21px;
    color: var(--gold);
    line-height: 1.05;
  }
  .person__role { font-size: 16px; color: var(--white); }
  .contacts {
    position: absolute;
    right: 34px; top: 222px;
    list-style: none;
    text-align: right;
  }
  .contacts li {
    font-size: 16px;
    color: var(--white);
    line-height: 24px;
    display: flex; justify-content: flex-end; align-items: center; gap: 10px;
  }
  .contacts .icon { width: 14px; height: 14px; flex: none; }
  .contacts .spacer { width: 14px; flex: none; }
</style>
</head>
<body>

<section class="card card--front">
  <div class="front-mark">
    <span class="front-mark__square" aria-hidden="true"></span>
    <span class="front-mark__name">Frame Line Studio</span>
  </div>
  <p class="front-web">www.framelinestudio.com.au</p>
</section>

<section class="card card--back">
  <div class="back-mark">
    <span class="back-mark__square" aria-hidden="true"></span>
    <p class="back-mark__name">Frame<br>Line<br>Studio</p>
  </div>

  <div class="brand">
    <p class="brand__name">Frame Line Studio</p>
    <p class="brand__tagline">Architecture Corporate commercial</p>
  </div>

  <div class="person">
    <p class="person__name">Aaron Pike</p>
    <p class="person__role">Photographer</p>
  </div>

  <ul class="contacts">
    <li>0400123987
      <svg class="icon" viewBox="0 0 14 14" aria-hidden="true"><path d="M3 1h2.5l1 3-1.5 1a7 7 0 0 0 4 4l1-1.5 3 1V11a2 2 0 0 1-2 2A10 10 0 0 1 1 3a2 2 0 0 1 2-2z" fill="var(--gold)"/></svg>
    </li>
    <li>info@framelinestudio.com.au
      <svg class="icon" viewBox="0 0 14 14" aria-hidden="true"><rect x="1" y="3" width="12" height="8" fill="var(--gold)"/><path d="M1 3l6 4.5L13 3" fill="none" stroke="var(--card)" stroke-width="1.2"/></svg>
    </li>
    <li>www.framelinestudio.com.au
      <svg class="icon" viewBox="0 0 14 14" aria-hidden="true"><circle cx="7" cy="7" r="6" fill="var(--gold)"/><path d="M1 7h12M7 1c-3 3-3 9 0 12M7 1c3 3 3 9 0 12" fill="none" stroke="var(--card)" stroke-width="0.9"/></svg>
    </li>
    <li>48 Harbour Rd Portland Vic 3305<span class="spacer"></span></li>
  </ul>
</section>

</body>
</html>
```